Business Card Design for Marketing Firm

Looking for business card design for higher end marketing firm. Clean but impressionable/trendy. We are a marketing firm that represents manufacturers in the foodservice equipment and supply industry. Our customers are end users such has hotels, restaurants, country clubs, convention centers and casinos as well as distributors of restaurants supplies and equipment, and manufacturers of foodservice equipment and supplies.
Target Market(s)
Hotels, Restaurants, Supply & Equipment Distributors, Foodservice Manufacturers
Industry/Entity Type
Foodservice/Hospitality
Contact Information for Business Card
Name, Title, Contact Number, Email, Website, Social Media, Address
Requirements
Must have
- Clean & Simple but Serious and Impressionable

```html
<!DOCTYPE html>
<html lang="en">
<head>
<meta charset="utf-8">
<title>Meridian Service Reps – Business Card</title>
<link rel="stylesheet" href="https://fonts.googleapis.com/css2?family=Libre+Baskerville:wght@700&family=Arimo:wght@400&display=swap">
<style>
  :root {
    --backdrop: #d3d6d7;
    --paper: #fbfbfa;
    --navy: #1c1f5e;
    --ink-grey: #5d5f66;
    --band-text: #e9eaf3;
  }
  * { box-sizing: border-box; margin: 0; padding: 0; }
  html, body { width: 1200px; height: 829px; overflow: hidden; }
  body {
    background: var(--backdrop);
    display: flex;
    align-items: center;
    justify-content: center;
    gap: 48px;
    font-family: "Arimo", Arial, sans-serif;
  }
  .card {
    position: relative;
    width: 525px;
    height: 300px;
    background: var(--paper);
    border-bottom: 4px solid var(--navy);
    box-shadow: 0 10px 24px rgba(0,0,0,0.12);
  }
  .brand-name {
    font-family: "Libre Baskerville", Georgia, serif;
    font-weight: 700;
    color: var(--navy);
    text-transform: uppercase;
    letter-spacing: 0.04em;
    text-align: center;
    line-height: 1.25;
  }
  /* Front */
  .card-front .brand-name {
    position: absolute;
    top: 42px;
    left: 0;
    width: 100%;
    font-size: 20px;
  }
  .card-front .brand-name small {
    display: block;
    font-size: 12px;
    letter-spacing: 0.12em;
  }
  .person {
    position: absolute;
    top: 128px;
    right: 280px;
    text-align: right;
  }
  .person-name {
    font-family: "Libre Baskerville", Georgia, serif;
    font-weight: 700;
    color: var(--navy);
    font-size: 17px;
    text-transform: uppercase;
    letter-spacing: 0.02em;
  }
  .person-title {
    margin-top: 6px;
    font-size: 13px;
    color: var(--ink-grey);
  }
  .divider {
    position: absolute;
    top: 124px;
    left: 258px;
    width: 1px;
    height: 80px;
    background: var(--navy);
  }
  .contacts {
    position: absolute;
    top: 124px;
    left: 272px;
    list-style: none;
    font-size: 12.5px;
    color: var(--ink-grey);
  }
  .contacts li {
    display: flex;
    align-items: center;
    gap: 6px;
    height: 20px;
  }
  .contacts svg { width: 10px; height: 10px; fill: var(--navy); flex: none; }
  .social-dot {
    width: 9px; height: 9px; border-radius: 50%;
    background: var(--navy); flex: none;
  }
  .address-band {
    position: absolute;
    left: 0;
    top: 226px;
    width: 100%;
    height: 30px;
    background: var(--navy);
    color: var(--band-text);
    font-size: 13px;
    display: flex;
    align-items: center;
    padding-left: 96px;
  }
  /* Back */
  .card-back {
    display: flex;
    align-items: center;
    justify-content: center;
  }
  .card-back .brand-name { font-size: 26px; }
  .card-back .brand-name small {
    display: block;
    font-size: 16px;
    letter-spacing: 0.14em;
    margin-top: 2px;
  }
</style>
</head>
<body>
  <section class="card card-front" aria-label="Business card front">
    <div class="brand-name">Meridian Service<small>Reps</small></div>

    <div class="person">
      <div class="person-name">Daniel Whitford</div>
      <div class="person-title">CEO/Founder</div>
    </div>

    <div class="divider"></div>

    <ul class="contacts">
      <li>
        <svg viewBox="0 0 10 10" aria-hidden="true"><path d="M1 2.5 Q1 1 2.5 1 L3.5 1 L4.3 3 L3.2 3.8 Q4 5.6 6.2 6.8 L7 5.7 L9 6.5 L9 7.5 Q9 9 7.5 9 Q1 8.5 1 2.5Z"/></svg>
        555-204-7731
      </li>
      <li>
        <svg viewBox="0 0 10 10" aria-hidden="true"><path d="M0.5 2 H9.5 V8 H0.5Z M1.2 2.6 L5 5.4 L8.8 2.6" fill="none" stroke="#1c1f5e" stroke-width="1"/></svg>
        info@meridianservicereps.com
      </li>
      <li>
        <svg viewBox="0 0 10 10" aria-hidden="true"><circle cx="5" cy="5" r="4.3" fill="none" stroke="#1c1f5e" stroke-width="1"/><path d="M0.7 5 H9.3 M5 0.7 Q2.5 5 5 9.3 Q7.5 5 5 0.7" fill="none" stroke="#1c1f5e" stroke-width="0.8"/></svg>
        www.meridianservicereps.com
      </li>
      <li>
        <span class="social-dot"></span>
        @meridianservicereps
      </li>
    </ul>

    <div class="address-band">45 Harbor Lane, Suite 210 Eastfield, CD 30812</div>
  </section>

  <section class="card card-back" aria-label="Business card back">
    <div class="brand-name">Meridian Service<small>Reps</small></div>
  </section>
</body>
</html>
```